Boutique custom software development company needs new business card

Our nearly 20 year old custom software development company would like to better include the fact that we are now providing Bitcoin services. These new services are B2B include education (how to acquire and securely hold Bitcoin) and integrating Bitcoin payments into existing ecommerce sites or other existing systems. Please keep the card clean and simple. Attached is our current design and some other files. vextorial.com

Target Market(s)

businesses owners interested in long term relationship

Industry/Entity Type

Custom software development and Bitcoin

Contact Information for Business Card

Dale Parker, dale@vextorial.com, vextorial.com, (888) 555-VXTRL

Font styles to use
Other font styles liked:
• monospace

Requirements
Must have
• double-sided
Nice to have
• clean and simple
Should not have
• physical address

```html
<!DOCTYPE html>
<html lang="en">
<head>
<meta charset="utf-8">
<title>Vextorial Business Card</title>
<link rel="stylesheet" href="https://fonts.googleapis.com/css2?family=Montserrat:wght@400;500;600;700&family=Lato:wght@300;400&display=swap">
<style>
  :root {
    --bg: #cfd5d5;
    --brand-blue: #3268b1;
    --brand-orange: #e8671c;
    --paper: #f7f7f6;
    --ink: #4a4d52;
    --white: #ffffff;
  }
  * { box-sizing: border-box; margin: 0; padding: 0; }
  html, body { width: 1200px; height: 1050px; overflow: hidden; }
  body {
    background: var(--bg);
    font-family: "Montserrat", sans-serif;
    position: relative;
  }
  .card {
    position: absolute;
    left: 340px;
    width: 520px;
    height: 297px;
    border-radius: 3px;
    box-shadow: 0 10px 24px rgba(0,0,0,0.12);
    overflow: hidden;
  }
  .card--front { top: 190px; background: var(--paper); }
  .card--back { top: 560px; background: var(--brand-blue); }

  /* Front */
  .front-mark {
    position: absolute;
    left: 54px;
    top: 78px;
    display: flex;
    flex-direction: column;
    align-items: flex-start;
    gap: 12px;
  }
  .front-mark__square {
    width: 118px;
    height: 118px;
    background: var(--brand-blue);
  }
  .front-mark__name {
    font-family: "Montserrat", sans-serif;
    font-weight: 700;
    font-size: 20px;
    color: var(--brand-blue);
    letter-spacing: 0.5px;
  }
  .contact {
    position: absolute;
    left: 282px;
    top: 108px;
    color: var(--ink);
    font-size: 12.5px;
    line-height: 1.5;
  }
  .contact__name {
    font-weight: 600;
    font-size: 21px;
    letter-spacing: 0.5px;
    line-height: 1.1;
  }
  .contact__first { color: var(--brand-orange); }
  .contact__last { color: var(--brand-blue); }
  .contact__title {
    font-size: 12px;
    letter-spacing: 0.8px;
    margin-bottom: 8px;
  }
  .contact__line { display: flex; align-items: center; gap: 6px; }
  .contact__icon { width: 10px; height: 10px; flex: none; }

  /* Back */
  .wordmark {
    position: absolute;
    left: 0; right: 0;
    top: 108px;
    text-align: center;
  }
  .wordmark__name {
    font-family: "Montserrat", sans-serif;
    font-weight: 700;
    font-size: 52px;
    color: var(--white);
    letter-spacing: 2px;
    line-height: 1;
  }
  .wordmark__tagline {
    font-family: "Lato", sans-serif;
    font-weight: 400;
    font-size: 17px;
    color: var(--white);
    margin-top: 8px;
    letter-spacing: 0.3px;
  }
</style>
</head>
<body>
  <section class="card card--front">
    <div class="front-mark">
      <div class="front-mark__square"></div>
      <div class="front-mark__name">Vextorial</div>
    </div>
    <div class="contact">
      <div class="contact__name"><span class="contact__first">DALE</span> <span class="contact__last">PARKER</span></div>
      <div class="contact__title">DIRECTOR</div>
      <div class="contact__line">
        <svg class="contact__icon" viewBox="0 0 10 10"><path d="M2 0.8 L3.6 0.8 L4.2 3 L3 3.8 Q4 6 6.2 7 L7 5.8 L9.2 6.4 L9.2 8 Q9.2 9.2 8 9.2 Q1 8.6 0.8 2 Q0.8 0.8 2 0.8 Z" fill="var(--brand-blue)"/></svg>
        <span>(888) 555-VXTRL</span>
      </div>
      <div class="contact__line">
        <svg class="contact__icon" viewBox="0 0 10 10"><rect x="0.8" y="2" width="8.4" height="6" fill="none" stroke="var(--brand-blue)" stroke-width="1"/><path d="M0.8 2 L5 5.5 L9.2 2" fill="none" stroke="var(--brand-blue)" stroke-width="1"/></svg>
        <span>dale@vextorial.com</span>
      </div>
      <div class="contact__line">
        <svg class="contact__icon" viewBox="0 0 10 10"><circle cx="5" cy="5" r="4.2" fill="none" stroke="var(--brand-blue)" stroke-width="1"/><ellipse cx="5" cy="5" rx="1.8" ry="4.2" fill="none" stroke="var(--brand-blue)" stroke-width="0.8"/><path d="M0.8 5 H9.2" stroke="var(--brand-blue)" stroke-width="0.8"/></svg>
        <span>www.vextorial.com</span>
      </div>
    </div>
  </section>

  <section class="card card--back">
    <div class="wordmark">
      <div class="wordmark__name">VEXTORIAL</div>
      <div class="wordmark__tagline">custom applications &amp; bitcoin services</div>
    </div>
  </section>
</body>
</html>
```